Local Roofing/Construction company business needs new biz card design

We need a new business card design, current cards are from the start of this operation and generic at best. We are a local Construction Company (General Contractor) with a majority of our work originating from insurance claims-exterior finish work is the main focus (Roofs-Siding-Gutters etc). Heavily involved with homeowners and the low ball offers they receive from insurance company's after a insurable event takes place. I have attached some of our original logo file(s) below.

```html
<!DOCTYPE html>
<html lang="en">
<head>
<meta charset="utf-8">
<title>Northgate Builders – Business Card</title>
<link href="https://fonts.googleapis.com/css2?family=Rajdhani:wght@600;700&family=Open+Sans:wght@400;600&display=swap" rel="stylesheet">
<style>
  :root {
    --green: #31d77c;
    --green-deep: #27c46d;
    --green-soft: #3fe08a;
    --white: #ffffff;
    --ink: #2b2b2b;
    --ink-soft: #4a4a4a;
    --stage: #d4d4d4;
  }
  * { box-sizing: border-box; margin: 0; padding: 0; }
  html, body { width: 1200px; height: 800px; overflow: hidden; }
  body {
    background: linear-gradient(135deg, #bdbdbd 0%, var(--stage) 60%, #e2e2e2 100%);
    position: relative;
    font-family: "Open Sans", Arial, sans-serif;
  }
  .card {
    position: absolute;
    width: 540px;
    height: 310px;
    border-radius: 22px;
    overflow: hidden;
    box-shadow: 0 14px 30px rgba(0,0,0,0.22);
  }

  /* Front */
  .card-front {
    left: 40px; top: 110px;
    background: var(--white);
    border: 3px solid var(--green);
  }
  .band-top {
    position: absolute; left: 480px; top: 70px;
    width: 60px; height: 62px;
    background: var(--green);
  }
  .band-contact {
    position: absolute; left: 0; top: 152px;
    width: 340px; height: 74px;
    background: var(--green);
  }
  .logo-block {
    position: absolute; left: 320px; top: 50px;
    width: 170px; height: 180px;
    background: var(--green);
    clip-path: polygon(14% 0, 86% 0, 100% 12%, 100% 88%, 86% 100%, 14% 100%, 0 88%, 0 12%);
    display: flex; flex-direction: column; align-items: center; justify-content: center;
    gap: 10px;
  }
  .logo-square {
    width: 46px; height: 46px; background: var(--white);
  }
  .brand-name {
    font-family: "Rajdhani", "Arial Narrow", sans-serif;
    font-weight: 700;
    color: var(--white);
    text-align: center;
    line-height: 1;
    letter-spacing: 1px;
  }
  .brand-name .line-1 { display: block; font-size: 26px; }
  .brand-name .line-2 { display: block; font-size: 15px; letter-spacing: 2px; margin-top: 3px; }

  .person { position: absolute; left: 30px; top: 82px; }
  .person-name {
    font-family: "Rajdhani", "Arial Narrow", sans-serif;
    font-weight: 700; font-size: 25px;
    color: var(--green); letter-spacing: 1px;
    line-height: 1;
  }
  .person-role {
    font-size: 11.5px; color: var(--ink-soft);
    letter-spacing: 0.6px; margin-top: 4px;
  }
  .contact-list {
    position: absolute; left: 30px; top: 160px;
    list-style: none;
  }
  .contact-list li {
    display: flex; align-items: center; gap: 8px;
    font-size: 13.5px; color: var(--white);
    height: 19px; letter-spacing: 0.3px;
    white-space: nowrap;
  }
  .contact-list svg { width: 13px; height: 13px; flex: none; }
  .address {
    position: absolute; left: 30px; top: 246px;
    font-size: 15px; font-style: normal;
    color: var(--ink); line-height: 1.35;
    letter-spacing: 0.3px;
  }

  /* Back */
  .card-back {
    left: 620px; top: 380px;
    background: var(--green);
  }
  .back-texture {
    position: absolute; inset: 0;
    background: radial-gradient(circle at 30% 40%, var(--green-soft) 0%, var(--green) 55%, var(--green-deep) 100%);
  }
  .back-badge {
    position: absolute; left: 300px; top: 105px;
    width: 150px; height: 100px;
    border: 3px solid var(--white);
    border-radius: 10px;
    display: flex; flex-direction: column; align-items: center; justify-content: center;
    gap: 6px;
  }
  .back-badge .logo-square { width: 26px; height: 26px; }
  .back-badge .brand-name .line-1 { font-size: 20px; }
  .back-badge .brand-name .line-2 { font-size: 11px; }
</style>
</head>
<body>

  <section class="card card-front" aria-label="Business card front">
    <div class="band-top"></div>
    <div class="band-contact"></div>

    <div class="logo-block">
      <span class="logo-square"></span>
      <p class="brand-name"><span class="line-1">NORTHGATE</span><span class="line-2">BUILDERS</span></p>
    </div>

    <div class="person">
      <h1 class="person-name">DANIEL REYES</h1>
      <p class="person-role">MANAGING DIRECTOR</p>
    </div>

    <ul class="contact-list">
      <li>
        <svg viewBox="0 0 16 16" aria-hidden="true"><path fill="#fff" d="M3.6 1.5l2.2 2.4-1.3 1.8c.9 2 2.5 3.6 4.6 4.6l1.8-1.3 2.4 2.2-1.3 2.3C7 13.3 2.7 9 2.3 2.8z"/></svg>
        055-987 654 321
      </li>
      <li>
        <svg viewBox="0 0 16 16" aria-hidden="true"><rect x="1" y="3" width="14" height="10" fill="#fff"/><path d="M1.5 3.5L8 9l6.5-5.5" stroke="#31d77c" stroke-width="1.4" fill="none"/></svg>
        hello@northgatebuild.com
      </li>
      <li>
        <svg viewBox="0 0 16 16" aria-hidden="true"><circle cx="8" cy="8" r="6.5" fill="none" stroke="#fff" stroke-width="1.4"/><ellipse cx="8" cy="8" rx="2.8" ry="6.5" fill="none" stroke="#fff" stroke-width="1.2"/><path d="M1.5 8h13M2.5 5h11M2.5 11h11" stroke="#fff" stroke-width="1"/></svg>
        www.northgatebuild.com
      </li>
    </ul>

    <address class="address">88 Harbor Lane, Suite 4<br>30217, Springvale</address>
  </section>

  <section class="card card-back" aria-label="Business card back">
    <div class="back-texture" role="img" aria-label="Repeating embossed brand pattern in green tones"></div>
    <div class="back-badge">
      <span class="logo-square"></span>
      <p class="brand-name"><span class="line-1">NORTHGATE</span><span class="line-2">BUILDERS</span></p>
    </div>
  </section>

</body>
</html>
```